Velan Tea Label & packaging for a premium tea brand. For local and global market

Create a look and feel for a box and rectangle tin. We are looking for a luxe packaging design for a new tea brand based in Kenya called 'Velan Tea'. Kenya is home to the finest teas in the world and Velan tea looks to embody that fact. Velan Tea uses the most premium of Kenyan Tea, Black tea, Purple tea, White Tea, Green tea, Hibiscus Tea and Moringa Tea. Velan Tea is handpicked from Kenya's highlands. This project will include the look and feel of the different teas described above. The copy on the main face of the box should read 'Premium Kenyan Tea' The box will contain 25 tagged tea bags, with a net weight of 50 gms.

On one side of the box will read 'packaging instructions' To fully savour this Velan premium tea, use one tea bag for each cup, add some freshly bolded water and wait for 2 minutes as you enjoy the sweet aroma of our tea, stir and serve' Ingredients : Black Tea, and for the others the same : Hibiscus Tea, Green Tea, Purple Tea, White tea. should also feature on the label: Produce of Kenya.

Target Market(s)

Premium

Industry/Entity Type

Agribusiness

Font styles to use
Script

Colors

Designer to choose colors to be used in the design.

Requirements
Must have
• Luxe look and feel
Nice to have
• I have attached the Velan tea logo and images of brands I'd lile the designer to be inspired by.
Should not have
• Green and yellow colours

```html
<!DOCTYPE html>
<html lang="en">
<head>
<meta charset="UTF-8">
<title>Velan Tea – Premium Hibiscus Tea Tin</title>
<link rel="stylesheet" href="https://fonts.googleapis.com/css2?family=Cinzel:wght@400;500&family=Montserrat:wght@400;500&family=Roboto+Condensed:wght@300;400;700&display=swap">
<style>
  :root {
    --bg: #ffffff;
    --tin-pale: #f3e8ed;
    --lid-pale: #ece4ea;
    --rim: #b0607d;
    --rim-dark: #94476a;
    --mauve: #8d3a5c;
    --mauve-soft: #a85a7a;
    --splash-faint: #e7c9d5;
    --silver-light: #f1f1f3;
    --silver-mid: #c9c9cd;
    --silver-dark: #a9a9ae;
    --ink: #5a5a5e;
    --ink-dark: #3c3c40;
    --white: #ffffff;
  }
  * { box-sizing: border-box; margin: 0; padding: 0; }
  html, body { width: 1200px; height: 1200px; overflow: hidden; background: var(--bg); }
  .canvas { position: relative; width: 1200px; height: 1200px; }

  .panel { position: absolute; top: 160px; height: 880px; overflow: hidden; }
  .panel--side { left: 70px; width: 400px; }
  .panel--front { left: 490px; width: 640px; }

  .lid { position: absolute; top: 0; left: 0; right: 0; height: 120px;
    background: linear-gradient(180deg, #f6f0f4 0%, var(--lid-pale) 100%); }
  .rim { position: absolute; left: 0; right: 0; height: 18px;
    background: linear-gradient(180deg, var(--rim) 0%, var(--rim-dark) 100%); }
  .rim--top { top: 120px; }
  .rim--bottom { bottom: 0; }
  .body { position: absolute; top: 138px; left: 0; right: 0; bottom: 18px;
    background: linear-gradient(180deg, #f7eef2 0%, var(--tin-pale) 100%); }

  .splash { position: absolute; border-radius: 48% 52% 45% 55% / 52% 44% 56% 48%; }
  .splash--front { left: 110px; top: 50px; width: 420px; height: 400px;
    background: radial-gradient(circle at 50% 45%, #a44f73 0%, var(--mauve) 60%, #7a2f4e 100%); }
  .splash--side { left: -40px; top: 230px; width: 240px; height: 260px;
    background: radial-gradient(circle at 50% 50%, var(--splash-faint) 0%, #efdde5 100%); opacity: .85; }

  .brand { position: absolute; text-align: center; font-family: "Montserrat", sans-serif; font-weight: 400; }
  .brand--front { left: 110px; width: 420px; top: 175px; color: var(--white); }
  .brand--front .brand__name { font-size: 96px; letter-spacing: 2px; line-height: 1; }
  .brand--front .brand__sub { font-size: 50px; letter-spacing: 6px; margin-top: 10px; }
  .brand--side { left: 40px; top: 80px; color: var(--mauve-soft); text-align: left; }
  .brand--side .brand__name { font-size: 40px; line-height: 1; }
  .brand--side .brand__sub { font-size: 18px; letter-spacing: 3px; margin-top: 6px; }

  .info { position: absolute; right: 30px; width: 210px; text-align: right; font-family: "Roboto Condensed", sans-serif; }
  .info--instructions { top: 190px; }
  .info--ingredients { top: 370px; }
  .info__title { font-size: 14px; font-weight: 700; color: var(--mauve); text-transform: uppercase; margin-bottom: 5px; }
  .info__text { font-size: 13px; font-weight: 300; color: var(--ink-dark); line-height: 1.55; }

  .band-line { position: absolute; left: 0; right: 0; height: 7px;
    background: linear-gradient(180deg, var(--silver-mid), var(--silver-light), var(--silver-dark)); }
  .band-line--a { top: 500px; }
  .band-line--b { top: 605px; }
  .band { position: absolute; left: 0; right: 0; top: 515px; height: 82px;
    display: flex; align-items: center; justify-content: center;
    background: linear-gradient(180deg, var(--silver-mid) 0%, var(--silver-light) 45%, var(--silver-mid) 100%);
    font-family: "Cinzel", serif; color: var(--ink); }
  .band--front { font-size: 36px; letter-spacing: 3px; }
  .band--side { font-size: 26px; letter-spacing: 1px; }

  .net { position: absolute; left: 0; right: 0; top: 650px; text-align: center;
    font-family: "Montserrat", sans-serif; color: var(--mauve); letter-spacing: 1px; }
  .net--front { font-size: 17px; }
  .net--side { font-size: 12px; color: var(--ink); }
</style>
</head>
<body>
<div class="canvas">

  <section class="panel panel--side" aria-label="Side panel">
    <div class="lid"></div>
    <div class="rim rim--top"></div>
    <div class="body">
      <div class="splash splash--side" role="img" aria-label="Faint watercolour splash with tropical leaves"></div>
      <div class="brand brand--side">
        <div class="brand__name">Velan</div>
        <div class="brand__sub">Tea</div>
      </div>
      <div class="info info--instructions">
        <h3 class="info__title">Packaging Instructions</h3>
        <p class="info__text">To fully savour this Velan premium tea, use one tea bag for each cup, add some freshly bolded water and wait for 2 minutes as you enjoy the sweet aroma of our tea, stir and serve.</p>
      </div>
      <div class="info info--ingredients">
        <h3 class="info__title">Ingredients</h3>
        <p class="info__text">Hibiscus Tea</p>
      </div>
      <div class="band-line band-line--a"></div>
      <div class="band band--side">Premium Hibiscus Tea</div>
      <div class="band-line band-line--b"></div>
      <p class="net net--side">25 TEA BAGS (50 GMS)</p>
    </div>
    <div class="rim rim--bottom"></div>
  </section>

  <section class="panel panel--front" aria-label="Front panel">
    <div class="lid"></div>
    <div class="rim rim--top"></div>
    <div class="body">
      <div class="splash splash--front" role="img" aria-label="Mauve watercolour splash with tropical leaves and flowers"></div>
      <div class="brand brand--front">
        <div class="brand__name">VELAN</div>
        <div class="brand__sub">TEA</div>
      </div>
      <div class="band-line band-line--a"></div>
      <div class="band band--front">Premium Hibiscus Tea</div>
      <div class="band-line band-line--b"></div>
      <p class="net net--front">25 TEA BAGS (50 GMS)</p>
    </div>
    <div class="rim rim--bottom"></div>
  </section>

</div>
</body>
</html>
```